Merrowin Vodka logo and label design

We would like a logo and bottle label design for a new line of Ultra-Premium Vodka. The Company is called Merrowin Spirits and is based in Brisbane, Australia. We would like a 'Gatsby/Prohibition era vibe to the design. We want to keep it minimalistic and sleek. We strongly prefer a minimalist design and colour palette. Black,Gold,Grey,White,Silver,Red and Blue

The bottle will be similar in shape to Castellane/Blue Heron. There will also need to be space on the label for required information, as well as short bio of the company, which will be provided to the winning design.
Updates

We would like to add the polish code of arms for Opoczno. Have attached link for reference. https://www.crestarchive-demo.net/crestwiki/index.php?title=Opoczno

Target Market(s)

Luxury brand customers

Logo Text

Merrowin Ultra-Premium Vodka

Logo styles of interest
Wordmark Logo
Lettermark Logo
Requirements
Must have
• This is the first release from our new Vodka label. We want a logo and bottle label that reflects a premium product. We very much like Prohibition/Gatsby era themed bottles and labels. The label and bottle should be elegant and clean.
Should not have
• Anything too busy or confusing.

```html
<!DOCTYPE html>
<html lang="en">
<head>
<meta charset="utf-8">
<title>Merrowin Ultra-Premium Vodka – Logo and Label</title>
<link rel="stylesheet" href="https://fonts.googleapis.com/css2?family=Cinzel:wght@500&family=Josefin+Sans:wght@300&family=Oswald:wght@300&display=swap">
<style>
  :root {
    --ink: #1d1b1c;
    --tagline-grey: #6a6a6a;
    --crest-red: #e31b23;
    --pattern-light: #f2f2f2;
    --pattern-mid: #cfcfcf;
    --paper: #ffffff;
  }
  html, body {
    margin: 0;
    padding: 0;
    width: 1200px;
    height: 1000px;
    overflow: hidden;
    background: var(--paper);
  }
  .canvas {
    position: relative;
    width: 1200px;
    height: 1000px;
    background: var(--paper);
  }
  .lockup {
    position: absolute;
    left: 378px;
    width: 445px;
  }
  .lockup--logo { top: 110px; height: 260px; }
  .lockup--label { top: 473px; height: 410px; }

  .wordmark {
    position: absolute;
    left: 8px;
    top: 22px;
    margin: 0;
    font-family: "Cinzel", serif;
    font-weight: 500;
    font-size: 66px;
    line-height: 1;
    letter-spacing: 0.01em;
    color: var(--ink);
  }
  .tagline {
    position: absolute;
    left: 14px;
    top: 104px;
    margin: 0;
    font-family: "Josefin Sans", sans-serif;
    font-weight: 300;
    font-size: 21px;
    letter-spacing: 0.19em;
    color: var(--tagline-grey);
    white-space: nowrap;
  }
  .divider {
    position: absolute;
    left: 4px;
    top: 142px;
    width: 440px;
    height: 8px;
  }
  .crest-mark {
    position: absolute;
    left: 177px;
    top: 148px;
    width: 91px;
    height: 91px;
    background: var(--crest-red);
  }
  .arc-pattern {
    position: absolute;
    left: 116px;
    top: 148px;
    width: 212px;
    height: 257px;
    border-radius: 0 0 106px 106px;
    background: linear-gradient(180deg, var(--pattern-light), var(--pattern-mid));
  }
  .lockup--label .crest-mark { z-index: 1; }
  .spec {
    position: absolute;
    top: 180px;
    margin: 0;
    font-family: "Oswald", sans-serif;
    font-weight: 300;
    font-size: 19px;
    line-height: 1;
    color: var(--ink);
  }
  .spec--strength { left: 4px; }
  .spec--volume { right: 2px; }
</style>
</head>
<body>
  <main class="canvas">

    <section class="lockup lockup--logo" aria-label="Merrowin logo">
      <h1 class="wordmark">MERROWIN</h1>
      <p class="tagline">ULTRA- PREMIUM VODKA</p>
      <svg class="divider" viewBox="0 0 440 8" aria-hidden="true">
        <path d="M0 4 Q220 -1 440 4 Q220 9 0 4 Z" fill="var(--ink)"/>
      </svg>
      <div class="crest-mark" aria-hidden="true"></div>
    </section>

    <section class="lockup lockup--label" aria-label="Merrowin bottle label">
      <h2 class="wordmark">MERROWIN</h2>
      <p class="tagline">ULTRA- PREMIUM VODKA</p>
      <svg class="divider" viewBox="0 0 440 8" aria-hidden="true">
        <path d="M0 4 Q220 -1 440 4 Q220 9 0 4 Z" fill="var(--ink)"/>
      </svg>
      <div class="arc-pattern" role="img" aria-label="Cascading pattern of fine grey concentric arches beneath the crest"></div>
      <div class="crest-mark" aria-hidden="true"></div>
      <p class="spec spec--strength">40% alc</p>
      <p class="spec spec--volume">500ml e</p>
    </section>

  </main>
</body>
</html>
```